a customWebsite for our live Escape room with landing page and then links to the multiple locations

We are looking for a new main landing page that then goes to the location site So puzzlevaultery.com (main landing page)
The site needs to have main company info locations to choose a countdown clock and book now option news articles and video, a link to social media.
a link to the locations
the locations page will go to puzzlevaulterydm.com or puzzlevaulterymke.com for the des moines location and the milwaukee location with more locations opening soon. The location pages need to have a one page theme with book now options and social media links. We are a escape room company please visit puzzlevaulterydm.com to get a idea of what we are looking for. We want to work with someone that can also do updates as we add new rooms etc.. Also must be able to design and upload the site to godaddy for us. We would like the countdown timer to display a message at the end (promo code etc) All pages need to link back to the main page and the Des moines Location needs to link to qrtdesmoines.com. We are looking for a interactive responsive site that shows what we are. The room bios for the MKE location will be upfoaded soon the rooms for des moines are on puzzlevaulterydm.com. please google escape rooms and visit competitor sites to help get more ideas we are open to color changes or logo changes we just shared a video and article on facebook to help http://www.prairiegazette-news.com/story/entertainment/2015/02/19/puzzle-vaultery-des-moines/58214706/

Reason: Not one design has had a landing page with the links to the locations etc....

Reason: Still looking for a main page for puzzle vaultery on the main landing page stuff about escape games news stories who should try also a video feed and countdown timmer then a link to des moines and Milwaukee location on the milwaukee page info on the location and the rooms with a book now option. on the des moines location info on the location and rooms with a book now location pages should have links to facebook twitter for that location

Target Market(s)

Customers looking for information about our escape rooms

Industry/Entity Type

It Company

Number of Pages Required

4 page

Requirements
Must have
• main landing page, Des Moines Location Page, Milwaukee Location Page
• booking page
Nice to have
• Be creative look at our page and other pages related to escape rooms to get ideas

```html
<!DOCTYPE html>
<html lang="en">
<head>
<meta charset="utf-8">
<title>Puzzle Vaultery Des Moines</title>
<link href="https://fonts.googleapis.com/css2?family=Roboto:wght@400;500;700;900&display=swap" rel="stylesheet">
<style>
:root{
  --yellow:#f7c51b;
  --ink:#1a1a1a;
  --text:#333333;
  --muted:#666666;
  --dark:#101010;
  --band:#efefef;
  --band-deep:#e4e4e4;
  --white:#ffffff;
  --line:#d9d9d9;
}
*{box-sizing:border-box;margin:0;padding:0}
html,body{width:1200px;height:4296px;overflow:hidden}
body{font-family:"Roboto",Arial,sans-serif;color:var(--text);background:var(--white);position:relative}
a{color:inherit;text-decoration:none}
.topbar{height:118px;background:var(--dark);display:flex;align-items:center;justify-content:space-between;padding:0 100px}
.brand{display:flex;align-items:center;gap:14px}
.brand-mark{width:56px;height:56px;background:var(--yellow)}
.brand-name{color:var(--white);font-weight:700;font-size:22px;letter-spacing:1px;line-height:1.15;text-transform:uppercase}
.btn-book-top{background:var(--yellow);color:var(--ink);font-weight:700;font-size:16px;padding:14px 26px;display:flex;align-items:center;gap:12px}
.nav{height:60px;background:var(--white);display:flex;align-items:stretch;padding:0 86px;border-bottom:1px solid var(--line)}
.nav a{font-size:12px;font-weight:500;color:var(--ink);display:flex;align-items:center;padding:0 18px;text-transform:uppercase;white-space:nowrap}
.nav a.active{background:var(--yellow)}
.hero{height:646px;position:relative;background:linear-gradient(180deg,#3f4246 0%,#8a8c8e 40%,#5c5d5e 70%,#2b2b2b 100%);overflow:hidden}
.hero-dots{position:absolute;left:96px;top:240px;display:flex;flex-direction:column;gap:14px}
.hero-dots span{width:13px;height:13px;border-radius:50%;background:var(--white)}
.hero-dots span.on{background:transparent;border:2px solid var(--white)}
.play{position:absolute;left:553px;top:232px}
.hero-title{position:absolute;top:444px;width:100%;text-align:center;color:var(--white);font-size:29px;font-weight:700;letter-spacing:.5px}
.countdown{position:absolute;top:502px;left:0;width:100%;display:flex;justify-content:center;align-items:center;gap:14px}
.countdown .digit{width:52px;height:72px;background:var(--white);color:var(--ink);font-size:34px;font-weight:700;display:flex;align-items:center;justify-content:center}
.countdown .sep{color:var(--white);font-size:34px;font-weight:700}
.section-title{text-align:center;font-size:15px;font-weight:700;color:var(--ink);text-transform:uppercase}
.section-title::after{content:"";display:block;width:60px;height:3px;background:var(--yellow);margin:14px auto 0}
.who{height:542px;padding-top:44px}
.audience{display:flex;gap:37px;padding:0 100px;margin-top:48px}
.audience-card{width:221px}
.photo{height:180px}
.card-title{font-size:13px;font-weight:700;color:var(--ink);margin:18px 0 8px;text-transform:uppercase}
.card-text{font-size:13px;line-height:1.55;height:104px;overflow:hidden}
.btn-outline{display:inline-block;border:2px solid var(--yellow);color:var(--ink);font-size:11px;font-weight:700;padding:10px 14px;text-transform:uppercase;margin-top:8px}
.about{height:352px;background:var(--band);padding-top:40px;text-align:center}
.about-text{width:1040px;margin:38px auto 0;font-size:14px;line-height:1.75}
.about .btn-outline{margin-top:22px}
.rooms{height:625px;padding-top:44px}
.arrows{display:flex;justify-content:center;gap:10px;margin-top:22px}
.arrows span{width:34px;height:34px;border:1px solid var(--line);display:flex;align-items:center;justify-content:center;background:var(--white)}
.room-list{display:flex;gap:30px;padding:0 103px 0 100px;margin-top:30px}
.room{width:312px}
.room .photo{height:176px}
.room-title{font-size:13px;font-weight:700;color:var(--ink);margin-top:22px;text-transform:uppercase}
.room-meta{font-size:12px;font-weight:500;color:var(--ink);margin:6px 0 10px;text-transform:uppercase}
.room-text{font-size:13px;line-height:1.55;height:92px;overflow:hidden}
.room .btn-outline{margin-top:26px;padding:10px 20px}
.press{height:464px;background:var(--band);padding-top:44px;position:relative;text-align:center}
.avatar{width:110px;height:110px;border-radius:50%;margin:28px auto 0;background:linear-gradient(180deg,#d9d9d9,#3a3a3a)}
.press-heading{font-size:14px;font-weight:700;color:var(--ink);margin-top:16px;text-transform:uppercase}
.press-text{width:830px;margin:16px auto 0;font-size:13px;line-height:1.7}
.press .btn-outline{margin-top:18px}
.press-arrow{position:absolute;top:236px}
.faq{height:438px;background:var(--band-deep);padding-top:44px}
.faq-cols{display:flex;padding:0 100px;margin-top:30px}
.faq-item{display:flex;gap:16px;width:340px;padding-right:20px}
.faq-item + .faq-item{border-left:1px solid #cfcfcf;padding-left:18px}
.faq-icon{width:20px;height:20px;background:var(--yellow);flex:none;display:flex;align-items:center;justify-content:center}
.faq-q{font-size:13px;font-weight:700;color:var(--ink);text-transform:uppercase;margin-top:2px}
.faq-a{font-size:13px;line-height:1.6;margin-top:10px}
.contact{height:865px;padding-top:36px;text-align:center}
.contact-line{font-size:13px;color:var(--ink);margin-top:6px}
.contact-line:first-of-type{margin-top:30px}
.map{width:879px;height:295px;margin:30px auto 0;background:linear-gradient(135deg,#e7e4dc,#d6d3ca 60%,#c9d3c4)}
.form{width:690px;margin:30px auto 0;display:flex;flex-wrap:wrap;justify-content:space-between;gap:12px 0}
.field{width:324px;height:60px;border:1px solid var(--line);font-size:12px;color:var(--muted);text-align:left;padding:20px}
.field.message{width:690px;height:175px}
.btn-send{display:inline-block;background:var(--yellow);color:var(--ink);font-weight:700;font-size:13px;width:152px;height:49px;line-height:49px;margin-top:30px;text-transform:uppercase}
.footer{height:186px;background:var(--dark);text-align:center;padding-top:30px;color:#8a8a8a;font-size:12px}
.social{display:flex;justify-content:center;gap:12px;margin-top:20px}
.social a{width:30px;height:30px;border-radius:50%;background:#2c2c2c}
.copyright{margin-top:26px;font-size:11px;color:#6a6a6a}
</style>
</head>
<body>

<header class="topbar">
  <a class="brand" href="http://puzzlevaultery.com">
    <div class="brand-mark"></div>
    <div class="brand-name">Puzzle Vaultery<br>Des Moines</div>
  </a>
  <a class="btn-book-top" href="#book">BOOK NOW
    <svg width="9" height="14" viewBox="0 0 9 14"><path d="M1 1l6 6-6 6" fill="none" stroke="#1a1a1a" stroke-width="2.5"/></svg>
  </a>
</header>

<nav class="nav">
  <a class="active" href="http://puzzlevaultery.com">Home</a>
  <a href="#about">About Us</a>
  <a href="#who">Who should try Puzzle Vaultery DM?</a>
  <a href="#rooms">Rooms</a>
  <a href="#press">Press Release</a>
  <a href="http://qrtdesmoines.com">QRT Des Moines</a>
  <a href="#faq">FAQ</a>
  <a href="#contact">Contact Us</a>
</nav>

<section class="hero" role="img" aria-label="Person in a hooded jacket standing on an empty road leading into misty hills">
  <div class="hero-dots"><span></span><span></span><span class="on"></span><span></span><span></span></div>
  <svg class="play" width="94" height="94" viewBox="0 0 94 94">
    <circle cx="47" cy="47" r="45" fill="rgba(255,255,255,.85)"/>
    <path d="M38 30v34l28-17z" fill="#3a3a3a"/>
  </svg>
  <h1 class="hero-title">CAN YOU ESCAPE IN 60 MIN?</h1>
  <div class="countdown">
    <div class="digit">5</div><div class="digit">4</div>
    <div class="sep">:</div>
    <div class="digit">3</div><div class="digit">2</div>
  </div>
</section>

<section class="who" id="who">
  <h2 class="section-title">Who should try Puzzle Vaultery DM??</h2>
  <div class="audience">
    <div class="audience-card">
      <div class="photo" role="img" aria-label="Gamer lit by a blue screen glow" style="background:linear-gradient(135deg,#0b2a55,#2a7ac0 60%,#0e1b33)"></div>
      <h3 class="card-title">Gamers &amp; Brainiacs</h3>
      <p class="card-text">Are people in awe of your gaming skills? Do you always seem to find yourself being the smartest person in the room?</p>
      <span class="btn-outline">Read more</span>
    </div>
    <div class="audience-card">
      <div class="photo" role="img" aria-label="Family jumping on a grassy field under a blue sky" style="background:linear-gradient(180deg,#3d7fd0,#8cc0ea 55%,#6ea447)"></div>
      <h3 class="card-title">Families</h3>
      <p class="card-text">Ever try to have a fun game night with the family, only to find that your living room could get disaster relief funding from the Relief Bureau...</p>
      <span class="btn-outline">Read more</span>
    </div>
    <div class="audience-card">
      <div class="photo" role="img" aria-label="Team of colleagues at an office table" style="background:linear-gradient(135deg,#cfcfcf,#8e8e8e 60%,#5a5a5a)"></div>
      <h3 class="card-title">Corporate/Team-Building</h3>
      <p class="card-text">Excluding time sleeping, the average American spends 53.4% of their day, at work. Over half of our waking hours are spent with coworkers...</p>
      <span class="btn-outline">Read more</span>
    </div>
    <div class="audience-card">
      <div class="photo" role="img" aria-label="Smiling couple outdoors" style="background:linear-gradient(135deg,#d9c7a6,#a67b55 55%,#6c4c34)"></div>
      <h3 class="card-title">Just Visiting</h3>
      <p class="card-text">You made it...your estimation...after the long flight, held hostage by a screaming 3 year old with lungs like Marla Deveaux, or the car ride that took</p>
      <span class="btn-outline">Read more</span>
    </div>
  </div>
</section>

<section class="about" id="about">
  <h2 class="section-title">About Us</h2>
  <p class="about-text">Puzzle Vaultery DM is like nothing you have ever seen before. Located on the south side of downtown Des Moines, Puzzle Vaultery DM is the real-life incarnation of movies like Snare, Hidden Relic, Inspector Graves, and The Cipher Canvas. Puzzles, riddles, and coded messages are your only means of escape, as this is more a mental challenge than physical. Successfully navigating the different scenarios of the rooms, require more than just brains, alone...you must learn to communicate and work together with your team members, if you want any hope of walking out the doors to freedom. Group sizes vary, based on each different scenario, and all ages are welcome;</p>
  <span class="btn-outline">Read more</span>
</section>

<section class="rooms" id="rooms">
  <h2 class="section-title">Rooms</h2>
  <div class="arrows">
    <span><svg width="8" height="12" viewBox="0 0 8 12"><path d="M6 1L1 6l5 5" fill="none" stroke="#555" stroke-width="1.5"/></svg></span>
    <span><svg width="8" height="12" viewBox="0 0 8 12"><path d="M2 1l5 5-5 5" fill="none" stroke="#555" stroke-width="1.5"/></svg></span>
  </div>
  <div class="room-list">
    <div class="room">
      <div class="photo" role="img" aria-label="Bright living room with wooden floors" style="background:linear-gradient(135deg,#e9dcc4,#b48a5c 60%,#7a5534)"></div>
      <h3 class="room-title">The Party Room</h3>
      <p class="room-meta">Min Players 1 — Max Players 12</p>
      <p class="room-text">Always looking for new ways to entertain his friends, Simon a lifelong enthusiast of puzzles, riddles and the like has gathered all of you together today, for a party at QRT Des Moines.</p>
      <a class="btn-outline" href="#book">Book now</a>
    </div>
    <div class="room">
      <div class="photo" role="img" aria-label="Two agents shaking hands across a desk" style="background:linear-gradient(135deg,#dfe4ea,#8e9aa6 55%,#3c4550)"></div>
      <h3 class="room-title">The Recruit</h3>
      <p class="room-meta">Min Players 1 — Max Players 8</p>
      <p class="room-text">Congratulations. You and your fellow agents have been hand-picked by top-brass officials to take part in the final selection stages for a "Blacklist" division of the SIA, known only as NICO.</p>
      <a class="btn-outline" href="#book">Book now</a>
    </div>
    <div class="room">
      <div class="photo" role="img" aria-label="Group of people in business suits" style="background:linear-gradient(180deg,#eeeeee,#9ea3a8 55%,#2f3338)"></div>
      <h3 class="room-title">The Collector</h3>
      <p class="room-meta">Min Players 1 — Max Players 12</p>
      <p class="room-text">A lifelong aficionado of sports memorabilia, recently posted an ad, with a variety of high dollar items for sale. As a fellow collector, you decide to answer this ad and meet with him, to discuss his</p>
      <a class="btn-outline" href="#book">Book now</a>
    </div>
  </div>
</section>

<section class="press" id="press">
  <h2 class="section-title">Press Release</h2>
  <div class="avatar" role="img" aria-label="Businessman in a dark suit"></div>
  <h3 class="press-heading">You have 60 minutes, can you escape?</h3>
  <p class="press-text">Des Moines, IA, December 11, 2014: Like a scene straight out of Hidden Relic, Snare, or The Cipher Canvas, it's a race against time at Puzzle Vaultery DM. Escape rooms are popping up all over the world. From Nashville to San Francisco, to Toronto and Singapore...people from all walks of life are testing their mental limits to escape before time runs out. The adrenaline-pumping experience at Puzzle Vaultery DM is no exception.</p>
  <span class="btn-outline">Read more</span>
  <svg class="press-arrow" style="left:170px" width="14" height="24" viewBox="0 0 14 24"><path d="M12 2L2 12l10 10" fill="none" stroke="#777" stroke-width="2.5"/></svg>
  <svg class="press-arrow" style="left:1018px" width="14" height="24" viewBox="0 0 14 24"><path d="M2 2l10 10-10 10" fill="none" stroke="#777" stroke-width="2.5"/></svg>
</section>

<section class="faq" id="faq">
  <h2 class="section-title">FAQ</h2>
  <div class="arrows">
    <span><svg width="8" height="12" viewBox="0 0 8 12"><path d="M6 1L1 6l5 5" fill="none" stroke="#555" stroke-width="1.5"/></svg></span>
    <span><svg width="8" height="12" viewBox="0 0 8 12"><path d="M2 1l5 5-5 5" fill="none" stroke="#555" stroke-width="1.5"/></svg></span>
  </div>
  <div class="faq-cols">
    <div class="faq-item">
      <span class="faq-icon"><svg width="7" height="10" viewBox="0 0 7 10"><path d="M1 1l4 4-4 4" fill="none" stroke="#1a1a1a" stroke-width="2"/></svg></span>
      <div><h3 class="faq-q">What is Puzzle Vaultery DM?</h3>
      <p class="faq-a">Puzzle Vaultery DM is a real-life escape room. Filled with puzzles, riddles, and hidden clues, it is the ultimate test of wits. Each group must work together to escape the room, using only their combined brain-power.</p></div>
    </div>
    <div class="faq-item">
      <span class="faq-icon"><svg width="7" height="10" viewBox="0 0 7 10"><path d="M1 1l4 4-4 4" fill="none" stroke="#1a1a1a" stroke-width="2"/></svg></span>
      <div><h3 class="faq-q">Am I really locked in a room?</h3>
      <p class="faq-a">Yes. You are really locked in a room. Well...kind of. At any time during the experience, should you need to leave the room, you can. Emergency exit buttons, located next to each exit door, will allow you to leave if the experience too intense</p></div>
    </div>
    <div class="faq-item">
      <span class="faq-icon"><svg width="7" height="10" viewBox="0 0 7 10"><path d="M1 1l4 4-4 4" fill="none" stroke="#1a1a1a" stroke-width="2"/></svg></span>
      <div><h3 class="faq-q">Are there any age restrictions?</h3>
      <p class="faq-a">We recommend participants be 10 and older, given the complexity of our puzzles and content of some of our themes. Some of our rooms may have more of a Horror theme. In the end, we ask the parents/guardians use their best judgement, when considering these rooms as an option for their children.</p></div>
    </div>
  </div>
</section>

<section class="contact" id="contact">
  <h2 class="section-title">Contact Us</h2>
  <p class="contact-line">1470 Elm Ridge Ave, Des Moines, IA, Puzzle Vaultery DM</p>
  <p class="contact-line">Phone: 515-555-0142 &nbsp;|&nbsp; Alt Phone: 515-555-0187 &nbsp;|&nbsp; Email: info@puzzlevaultery.com</p>
  <div class="map" role="img" aria-label="Street map of downtown Des Moines with a pin marking Puzzle Vaultery"></div>
  <div class="form" id="book">
    <div class="field">Name</div>
    <div class="field">E-Mail</div>
    <div class="field message">Message</div>
  </div>
  <span class="btn-send">Send</span>
</section>

<footer class="footer">
  <p>Follow us on</p>
  <div class="social"><a href="#" aria-label="Social page one"></a><a href="#" aria-label="Social page two"></a><a href="#" aria-label="Social page three"></a></div>
  <p class="copyright">2015 Puzzle Vaultery LLC. All rights reserved.</p>
</footer>

</body>
</html>
```